KTWG application splash screen

We need a 1024x768 image for use as an application splash screen.
The image will be displayed full screen on an 10 inch industrial PC 1024x768 screen while our application is launching. The image should convey that the application is "Waiting for connection to Wi-Fi access point..." and include a graphic of the industrial PC connected to the access point via an Ethernet cable. A list of troubleshooting steps should be included at the bottom of the image. The troubleshooting steps should not be the main focus of the image and should be shown in a smaller font (but still readable at 1024x768 displayed on a 10 inch screen).
I will include a mock up of the general idea of what we are looking for as well as image files for the industrial PC, a screenshot of our application to show on the PC's screen and the AP.
For general look and feel and a sense of corporate branding please review our website https://marrowgatesoilworks.example/. The splash screen should reflect corporate branding.
Target Market(s)
Users of our application
Industry/Entity Type
Agriculture
Look and feel

```html
<!DOCTYPE html>
<html lang="en">
<head>
<meta charset="utf-8">
<title>KTWG splash screen</title>
<link href="https://fonts.googleapis.com/css2?family=Kumbh+Sans:wght@400;600;700&family=Tinos:wght@400;700&display=swap" rel="stylesheet">
<style>
  :root {
    --stage: #111111;
    --field-green: #5cb37c;
    --ink: #0b0b0b;
    --white: #ffffff;
    --device-dark: #2c2c2e;
    --device-screen: #e8efe9;
    --antenna: #f1f1f1;
    --antenna-shade: #cfd3d2;
  }
  html, body {
    margin: 0;
    width: 1200px;
    height: 1200px;
    overflow: hidden;
    background: var(--stage);
  }
  .splash {
    position: absolute;
    left: 0;
    top: 150px;
    width: 1200px;
    height: 900px;
    background: var(--field-green);
    overflow: hidden;
    font-family: "Kumbh Sans", sans-serif;
    color: var(--ink);
  }
  .network-texture {
    position: absolute;
    right: 0;
    top: 0;
    width: 380px;
    height: 110px;
    background: radial-gradient(ellipse at 80% 20%, rgba(120,170,200,0.35), rgba(92,179,124,0) 70%);
  }
  .title {
    position: absolute;
    left: 0;
    right: 0;
    top: 46px;
    margin: 0;
    text-align: center;
    font-size: 45px;
    font-weight: 700;
    padding-left: 10px;
  }
  .cab-computer {
    position: absolute;
    left: 46px;
    top: 164px;
    width: 354px;
    height: 283px;
    border-radius: 16px;
    background: var(--device-dark);
  }
  .cab-computer::after {
    content: "";
    position: absolute;
    left: 32px;
    top: 26px;
    width: 286px;
    height: 210px;
    background: var(--device-screen);
    border-radius: 2px;
  }
  .access-point {
    position: absolute;
    left: 1029px;
    top: 143px;
    width: 50px;
    height: 307px;
    border-radius: 10px;
    background: linear-gradient(90deg, var(--antenna-shade), var(--antenna) 50%, var(--antenna-shade));
  }
  .link-diagram {
    position: absolute;
    left: 0;
    top: 0;
  }
  .cable-label {
    position: absolute;
    left: 0;
    right: 0;
    top: 496px;
    text-align: center;
    font-size: 26px;
    font-weight: 600;
    letter-spacing: 1.5px;
    padding-left: 76px;
  }
  .device-label {
    position: absolute;
    text-align: center;
    font-size: 28px;
    font-weight: 600;
    line-height: 33px;
  }
  .device-label.computer { left: 49px; width: 300px; top: 530px; }
  .device-label.ap { left: 897px; width: 300px; top: 530px; }
  .device-model {
    display: block;
    font-size: 21px;
    font-weight: 400;
    line-height: 30px;
  }
  .help {
    font-family: "Tinos", serif;
  }
  .help-heading {
    position: absolute;
    left: 54px;
    top: 657px;
    width: 239px;
    height: 39px;
    background: var(--white);
    border-radius: 6px;
    font-size: 21px;
    line-height: 39px;
    text-align: center;
  }
  .help-note {
    position: absolute;
    left: 59px;
    font-size: 20px;
    display: flex;
    align-items: center;
    gap: 6px;
  }
  .help-note::before {
    content: "";
    width: 12px;
    height: 12px;
    border: 1.5px solid var(--ink);
    border-radius: 50%;
    background: var(--white);
  }
  .help-note.first { top: 706px; }
  .help-note.second { top: 743px; }
  .step {
    position: absolute;
    top: 780px;
    height: 96px;
    box-sizing: border-box;
    padding: 8px 14px;
    background: var(--ink);
    color: var(--white);
    border-radius: 7px;
    font-size: 17px;
    line-height: 21px;
  }
  .step.one { left: 79px; width: 279px; }
  .step.two { left: 372px; width: 278px; }
  .step.three { left: 665px; width: 242px; }
  .step.four { left: 920px; width: 243px; }
</style>
</head>
<body>
  <main class="splash">
    <div class="network-texture" role="img" aria-label="Faint network of connected dots"></div>
    <h1 class="title">Waiting for Connection to Wi-Fi access point...</h1>

    <div class="cab-computer" role="img" aria-label="Rugged industrial tablet PC showing the KTWG seeding application"></div>
    <div class="access-point" role="img" aria-label="White outdoor Wi-Fi access point with two antennas"></div>

    <svg class="link-diagram" width="1200" height="900" viewBox="0 0 1200 900" aria-hidden="true">
      <g fill="none" stroke="#ffffff" stroke-width="4" stroke-linecap="round" stroke-dasharray="0 9">
        <path d="M214 470 V514 H503"/>
        <path d="M1053 470 V514 H782"/>
      </g>
      <circle cx="214" cy="457" r="10" fill="#0b0b0b" stroke="#ffffff" stroke-width="3"/>
      <circle cx="1053" cy="457" r="10" fill="#0b0b0b" stroke="#ffffff" stroke-width="3"/>
    </svg>
    <div class="cable-label">ETHERNET CABLE</div>

    <div class="device-label computer">Tractor cab<br>computer</div>
    <div class="device-label ap">Wi-Fi Access Point<span class="device-model">Northvale AP-225 Outdoor</span></div>

    <section class="help">
      <div class="help-heading">Troubleshooting steps:</div>
      <div class="help-note first">This screen should only be visible for a short time on boot.</div>
      <div class="help-note second">If this screen stays visible for more than a minute:</div>
      <div class="step one">Verify that the Wi-Fi Access Point (AP) powers up when this system does (indicated by a green light n the side of the AP).</div>
      <div class="step two">Check the Ethernet cable between this system and the AP for damage, and replace it if necessary.</div>
      <div class="step three">Power-cycle this system and wait for it to reboot fully.</div>
      <div class="step four">If the issue persists, contact KTWG support for further assistance.</div>
    </section>
  </main>
</body>
</html>
```